Create a capturing book cover for The Hollow Lantern

Book Title: The Hollow Lantern
Subtitle: Rising Past the Restless Tide
Author: Leshonda Marbury

Synopsis of book:
She didn’t really know what she wanted to do, but she knew she wanted to be successful. She struggled with identifying with what she was passionate about and what her purpose was for her life. Fear, turmoil, relationships, and career paths created turbulence in her long journey to fulfill her vision and lifetime goals. The Hollow Lantern exemplifies women who struggle with these things. The Hollow Lantern digs into the crevices of a blurry vision, disturbed, and fearful woman.

-The book focuses on a woman who is not necessarily physically cripple, but mentally, spiritually, and emotionally crippled.

The photos attached are just examples (not all have to be used)

Target Market(s)

Women who are dealing with barriers that are holding them back from reaching their goals or being successful

Font styles to use
Serif
Sans Serif

Colors
6b449b
b7a5cd

Requirements
Must have
• purple incorporated (not the full cover)
• I would like an African American woman, dominican woman, or mixed (you cannot tell what ethnicity she is) on the front cover if any.
Nice to have
• I would like the cover to tell the story. My ideas were maybe an actual crippled woman looking into the mirror at a woman who is at peace, or two women in one that shows one struggling and one living in happiness, or a crippled woman with her back turned and a path with something that symbolizes happiness at the end, or a lady sitting on the floor kind of distraught. I really want the designer to be creative. I do not have an exact image of what I want it to look like. These are just ideas. They do not have to be within the realms that I mentioned.
Should not have
• Extravagant text
• cartoon or animated pictures
• do not want a dark cover

```html
<!DOCTYPE html>
<html lang="en">
<head>
<meta charset="utf-8">
<title>The Hollow Lantern – Cover Wrap</title>
<link rel="stylesheet" href="https://fonts.googleapis.com/css2?family=Cinzel:wght@400;500&family=Cormorant+Garamond:wght@500&family=Tinos&display=swap">
<style>
  :root {
    --plum-deep: #2a0f3c;
    --plum: #4d1f68;
    --plum-light: #6b449b;
    --lavender: #b7a5cd;
    --mist: #d8cde0;
    --mist-light: #efeaf2;
    --ink: #2b1636;
    --cream: #f6eff6;
    --white: #ffffff;
    --shadow-tone: #5a4a66;
  }
  * { margin: 0; padding: 0; box-sizing: border-box; }
  html, body { width: 1200px; height: 928px; overflow: hidden; background: var(--white); }
  .cover-wrap { position: relative; width: 1200px; height: 928px; overflow: hidden; }

  /* Back cover + spine */
  .back {
    position: absolute; left: 0; top: 0; width: 627px; height: 928px;
    background: radial-gradient(ellipse at 30% 10%, var(--plum) 0%, var(--plum-deep) 75%);
    color: var(--cream);
  }
  .back-title { position: absolute; left: 60px; width: 450px; top: 60px; text-align: center; font-family: "Cinzel", serif; font-weight: 400; color: var(--cream); }
  .back-title .the { display: block; font-size: 20px; line-height: 24px; letter-spacing: 2px; }
  .back-title .line-one { display: block; font-size: 42px; line-height: 40px; letter-spacing: 4px; }
  .back-title .line-two { display: block; font-size: 42px; line-height: 42px; letter-spacing: 9px; }
  .back-subtitle { position: absolute; left: 60px; width: 450px; top: 182px; text-align: center; font-family: "Cinzel", serif; font-size: 22px; line-height: 26px; color: var(--cream); }
  .blurb { position: absolute; left: 72px; width: 438px; font-family: "Tinos", serif; font-size: 16.4px; line-height: 21.6px; text-align: justify; text-align-last: center; color: var(--cream); }
  .blurb-one { top: 266px; }
  .blurb-two { top: 562px; }
  .isbn-area { position: absolute; left: 323px; top: 750px; width: 225px; height: 135px; background: var(--white); }

  .spine { position: absolute; left: 555px; top: 0; width: 72px; height: 928px; }
  .spine-title, .spine-author {
    position: absolute; left: 50%; writing-mode: vertical-rl; transform: translateX(-50%);
    color: var(--cream); white-space: nowrap;
  }
  .spine-title { top: 38px; font-family: "Cinzel", serif; font-size: 31px; letter-spacing: 2.5px; }
  .spine-author { top: 655px; font-family: "Cormorant Garamond", serif; font-weight: 500; font-size: 27px; letter-spacing: 2.5px; }

  /* Front cover */
  .front {
    position: absolute; left: 627px; top: 0; width: 573px; height: 928px;
    background:
      radial-gradient(circle at 78% 6%, var(--white) 0%, rgba(255,255,255,0.6) 12%, rgba(255,255,255,0) 35%),
      linear-gradient(180deg, var(--mist-light) 0%, var(--mist) 55%, #cbbfd4 100%);
  }
  .front-author { position: absolute; left: 0; width: 573px; top: 52px; text-align: center; font-family: "Cormorant Garamond", serif; font-weight: 500; font-size: 33px; letter-spacing: 4px; color: var(--ink); padding-left: 10px; }
  .front-title { position: absolute; left: 28px; width: 540px; top: 218px; text-align: center; font-family: "Cinzel", serif; font-weight: 400; color: var(--ink); }
  .front-title .the { display: block; font-size: 42px; line-height: 42px; letter-spacing: 3px; padding-left: 30px; }
  .front-title .line-one { display: block; font-size: 72px; line-height: 76px; letter-spacing: 10px; }
  .front-title .line-two { display: block; font-size: 72px; line-height: 66px; letter-spacing: 12px; }
  .title-rule { position: absolute; left: 78px; top: 408px; width: 430px; height: 5px; }
  .front-subtitle { position: absolute; left: 80px; width: 430px; top: 423px; text-align: center; font-family: "Cinzel", serif; font-weight: 500; font-size: 22px; line-height: 26px; color: var(--plum); }

  .photo { position: absolute; }
  .dove-top { left: 138px; top: 165px; width: 112px; height: 70px; border-radius: 50%; background: radial-gradient(ellipse, rgba(255,255,255,0.85), rgba(255,255,255,0) 70%); }
  .dove-left { left: 108px; top: 508px; width: 80px; height: 96px; border-radius: 50%; background: radial-gradient(ellipse, rgba(255,255,255,0.85), rgba(255,255,255,0) 70%); }
  .dove-right { left: 425px; top: 497px; width: 95px; height: 68px; border-radius: 50%; background: radial-gradient(ellipse, rgba(255,255,255,0.85), rgba(255,255,255,0) 70%); }
  .woman-photo {
    left: 40px; top: 690px; width: 460px; height: 238px;
    background: radial-gradient(ellipse 55% 80% at 50% 100%, rgba(90,74,102,0.75) 0%, rgba(90,74,102,0.45) 50%, rgba(90,74,102,0) 100%);
  }
</style>
</head>
<body>
<main class="cover-wrap">
  <section class="back">
    <h2 class="back-title"><span class="the">The</span><span class="line-one">HOLLOW</span><span class="line-two">LANTERN</span></h2>
    <p class="back-subtitle">Rising Past the<br>Restless Tide</p>
    <p class="blurb blurb-one">Lorem ipsum dolor sit amet, consectetuer adipiscing elit. Aenean commodo ligula eget dolor. Aenean massa. Cum sociis natoque penatibus et magnis dis parturient montes, nascetur ridiculus mus. Donec quam felis, ultricies nec, pellentesque eu, pretium quis, sem. Nulla consequat massa quis enim. Donec pede justo, fringilla vel, aliquet nec, vulputate eget, arcu. In enim justo, rhoncus ut, imperdiet a, venenatis vitae, justo. Nullam dictum felis eu pede mollis pretium. Integer tincidunt. Cras dapibus. Vivamus elementum semper nisi. Aenean vulputate eleifend tellus. Aenean leo ligula, porttitor eu, consequat vitae, eleifend ac, enim.</p>
    <p class="blurb blurb-two">Aliquam lorem ante, dapibus in, viverra quis, feugiat a, tellus. Phasellus viverra nulla ut metus varius laoreet. Quisque rutrum. Aenean imperdiet. Etiam ultricies nisi vel augue. Curabitur ullamcorper ultricies nisi. Nam eget dui. Etiam rhoncus. Maecenas tempus, tellus eget condimentum rhoncus, sem quam semper libero, sit amet adipiscing sem neque sed ipsum.</p>
    <div class="isbn-area"></div>
    <div class="spine">
      <span class="spine-title">THE HOLLOW LANTERN</span>
      <span class="spine-author">Leshonda Marbury</span>
    </div>
  </section>

  <section class="front">
    <p class="front-author">Leshonda Marbury</p>
    <div class="photo dove-top" role="img" aria-label="White dove in flight"></div>
    <h1 class="front-title"><span class="the">The</span><span class="line-one">HOLLOW</span><span class="line-two">LANTERN</span></h1>
    <svg class="title-rule" viewBox="0 0 430 5" preserveAspectRatio="none" aria-hidden="true">
      <defs>
        <linearGradient id="rule-fade" x1="0" x2="1">
          <stop offset="0" stop-color="#6b449b" stop-opacity="0"/>
          <stop offset="0.15" stop-color="#4d1f68"/>
          <stop offset="0.85" stop-color="#4d1f68"/>
          <stop offset="1" stop-color="#6b449b" stop-opacity="0"/>
        </linearGradient>
      </defs>
      <rect x="0" y="1" width="430" height="3" fill="url(#rule-fade)"/>
    </svg>
    <p class="front-subtitle">Rising Past the<br>Restless Tide</p>
    <div class="photo dove-left" role="img" aria-label="White dove with wings raised"></div>
    <div class="photo dove-right" role="img" aria-label="White dove gliding"></div>
    <div class="photo woman-photo" role="img" aria-label="Photograph: woman seen from behind, head bowed, hair loose, in soft shadow"></div>
  </section>
</main>
</body>
</html>
```